A clean crisp business card for a Landscape Construction company. Designed to be easy to read contact/ info and also be appealing/interesting, unlike a traditional business card.

Industry/Entity Type

Landscape Construction

Contact Information for Business Card

Company name : Brambleford Landscape Construction, phone number: (877) 62Vista, website:Bramblefordyards.example, Email, sales@bramblefordyards.example

Requirements
Nice to have
• Luxurious finishes/ details…. Icons or emblems next to contact info
Should not have
• Clipart or general pictures

```html
<!DOCTYPE html>
<html lang="en">
<head>
<meta charset="utf-8">
<title>Brambleford Landscape Construction – Business Card</title>
<link href="https://fonts.googleapis.com/css2?family=Cinzel:wght@600&family=Jost:wght@400;500&display=swap" rel="stylesheet">
<style>
  :root {
    --backdrop: #9a9a9a;
    --card-white: #fbfbfa;
    --card-black: #2a2a2a;
    --edge-blue: #1f9fd6;
    --brand-blue: #2a6fc0;
    --brand-green: #8cc63f;
    --ink-grey: #4a4a4a;
    --rule-grey: #d6d6d6;
    --foil-silver: #a9a9a9;
  }
  * { margin: 0; padding: 0; box-sizing: border-box; }
  html, body {
    width: 1200px;
    height: 1078px;
    overflow: hidden;
    background: var(--backdrop);
  }
  .card {
    position: absolute;
    left: 220px;
    width: 760px;
    height: 434px;
    border-bottom: 8px solid var(--edge-blue);
    box-shadow: 0 14px 30px rgba(0,0,0,0.28);
  }
  .card--front { top: 70px; background: var(--card-white); }
  .card--back  { top: 570px; background: var(--card-black); }

  /* front: brand block */
  .brand {
    position: absolute;
    left: 60px;
    top: 0;
    width: 300px;
    height: 426px;
    display: flex;
    align-items: center;
    justify-content: center;
    gap: 12px;
  }
  .brand__dot {
    width: 14px; height: 14px;
    border-radius: 50%;
    background: var(--brand-blue);
    flex: none;
  }
  .brand__name {
    font-family: "Jost", sans-serif;
    font-weight: 500;
    font-size: 21px;
    line-height: 1.25;
    color: var(--brand-blue);
    letter-spacing: 0.5px;
  }
  .divider {
    position: absolute;
    left: 385px;
    top: 110px;
    width: 1px;
    height: 206px;
    background: var(--rule-grey);
  }

  /* front: person + contacts */
  .person {
    position: absolute;
    left: 420px;
    top: 120px;
  }
  .person__name {
    font-family: "Cinzel", serif;
    font-weight: 600;
    font-size: 27px;
    letter-spacing: 1px;
  }
  .person__first { color: var(--brand-blue); }
  .person__last  { color: var(--brand-green); }
  .person__title {
    font-family: "Jost", sans-serif;
    font-size: 16px;
    color: var(--ink-grey);
    margin-top: 2px;
  }
  .contacts {
    list-style: none;
    margin-top: 22px;
    font-family: "Jost", sans-serif;
    font-size: 16px;
    color: var(--ink-grey);
  }
  .contacts li {
    display: flex;
    align-items: center;
    gap: 10px;
    height: 24px;
  }
  .contacts svg { width: 14px; height: 14px; flex: none; fill: var(--brand-blue); }

  /* back */
  .back-brand {
    position: absolute;
    inset: 0 0 8px 0;
    display: flex;
    align-items: center;
    justify-content: center;
    gap: 16px;
  }
  .back-brand__dot {
    width: 18px; height: 18px;
    border-radius: 50%;
    background: var(--foil-silver);
  }
  .back-brand__name {
    font-family: "Jost", sans-serif;
    font-weight: 500;
    font-size: 34px;
    color: var(--foil-silver);
    letter-spacing: 1px;
  }
</style>
</head>
<body>
  <section class="card card--front">
    <div class="brand">
      <span class="brand__dot"></span>
      <span class="brand__name">Brambleford<br>Landscape Construction</span>
    </div>
    <div class="divider"></div>
    <div class="person">
      <div class="person__name"><span class="person__first">Daniel</span> <span class="person__last">Hartwell</span></div>
      <div class="person__title">President</div>
      <ul class="contacts">
        <li>
          <svg viewBox="0 0 24 24" aria-hidden="true"><path d="M6.6 10.8a15.1 15.1 0 0 0 6.6 6.6l2.2-2.2a1 1 0 0 1 1-.25 11.4 11.4 0 0 0 3.6.57 1 1 0 0 1 1 1V20a1 1 0 0 1-1 1A17 17 0 0 1 3 4a1 1 0 0 1 1-1h3.5a1 1 0 0 1 1 1c0 1.25.2 2.45.57 3.57a1 1 0 0 1-.25 1z"/></svg>
          (877) 62Vista
        </li>
        <li>
          <svg viewBox="0 0 24 24" aria-hidden="true"><path d="M2 5h20v14H2z M4 7v.4l8 5 8-5V7l-8 5z" fill-rule="evenodd"/></svg>
          sales@bramblefordyards.example
        </li>
        <li>
          <svg viewBox="0 0 24 24" aria-hidden="true"><circle cx="12" cy="12" r="10"/><path d="M2 12h20M12 2c3 3 3 17 0 20M12 2c-3 3-3 17 0 20" stroke="#fbfbfa" stroke-width="1.5" fill="none"/></svg>
          Bramblefordyards.example
        </li>
      </ul>
    </div>
  </section>

  <section class="card card--back">
    <div class="back-brand">
      <span class="back-brand__dot"></span>
      <span class="back-brand__name">Brambleford Landscape Construction</span>
    </div>
  </section>
</body>
</html>
```